AnswerCraft Website Redesign

I'm looking to redesign our website AnswerCraft.com. The main goal is to give it a fresh design that is easy on the eyes and pushes the users to creating an account.

Our platform is very simple and we only do one thing, we use ai to generate response to customer and product reviews.

See attached file to see the pricing section style.

On the homepage just under the hero section, I would like to include the wording:
"Write replies to the reviews you get on sites like:" then show the logos like we have on our register page: https://app.answercraft.com/public/index.php

Target Market(s)

Business owners with brick and morter business or any business or product that gets online reviews

Industry/Entity Type

reputation management

Number of Pages Required

2 page

Requirements
Must have
• Home page and pricing page

```html
<!DOCTYPE html>
<html lang="en">
<head>
<meta charset="utf-8">
<title>AnswerCraft — AI replies to your reviews</title>
<link rel="stylesheet" href="https://fonts.googleapis.com/css2?family=Montserrat:wght@500;600;700;800&family=Open+Sans:wght@400;600&display=swap">
<style>
  :root{
    --navy:#1c3a91;
    --navy-deep:#13296e;
    --orange:#f5a111;
    --orange-soft:#f7b23a;
    --ink:#1c1c1c;
    --text:#4a4a4a;
    --muted:#777;
    --line:#e3e3e3;
    --white:#ffffff;
    --footer:#090d1f;
    --head:"Montserrat",sans-serif;
    --body:"Open Sans",sans-serif;
  }
  *{box-sizing:border-box;margin:0;padding:0}
  html,body{width:1200px;height:4608px;overflow:hidden}
  body{position:relative;font-family:var(--body);color:var(--text);background:var(--white)}
  .abs{position:absolute}
  section,header,footer{position:absolute;left:0;width:1200px}
  h1,h2,h3,h4{font-family:var(--head);color:var(--ink)}

  /* top bar */
  .topbar{top:0;height:52px;background:var(--white)}
  .topbar-left{position:absolute;left:0;top:0;height:52px;width:700px;background:var(--navy);clip-path:polygon(0 0,100% 0,95% 100%,0 100%)}
  .topbar-accent{position:absolute;left:665px;top:0;width:535px;height:5px;background:var(--orange)}
  .topbar-item{position:absolute;top:17px;display:flex;align-items:center;gap:8px;font-size:13px;color:var(--white)}
  .topbar-item svg{width:13px;height:13px;fill:var(--white)}
  .topbar-sep{position:absolute;left:262px;top:10px;width:1px;height:32px;background:rgba(255,255,255,.6)}
  .topbar-login{position:absolute;left:910px;top:17px;font-size:12px;color:var(--ink)}
  .topbar-divider{position:absolute;left:990px;top:12px;width:1px;height:28px;background:#bbb}
  .topbar-social{position:absolute;left:1008px;top:20px;display:flex;gap:9px}
  .topbar-social span{width:10px;height:10px;border-radius:50%;background:var(--ink)}

  /* nav */
  .site-nav{top:52px;height:96px;background:var(--white);border-bottom:1px solid var(--line)}
  .brand{position:absolute;display:flex;align-items:center;gap:12px;font-family:var(--head);font-weight:800;font-size:30px;color:var(--navy)}
  .brand-mark{width:34px;height:34px;background:var(--orange)}
  .site-nav .brand{left:114px;top:29px}
  .nav-link{position:absolute;top:40px;font-size:15px;color:var(--ink)}
  .btn-try{position:absolute;left:975px;top:28px;width:114px;height:42px;background:var(--orange);border-radius:6px;font-family:var(--head);font-weight:700;font-size:14px;color:var(--ink);display:flex;align-items:center;justify-content:center}

  /* hero */
  .hero{top:148px;height:571px;background:linear-gradient(100deg,#2b2520 0%,#3e3a3a 40%,#5a4e48 70%,#2d2a29 100%)}
  .hero-eyebrow{position:absolute;left:114px;top:142px;font-family:var(--head);font-weight:700;font-size:19px;color:var(--orange)}
  .hero-title{position:absolute;left:112px;top:176px;width:520px;font-weight:800;font-size:48px;line-height:57px;color:var(--white)}
  .btn-primary{position:absolute;background:var(--navy);color:var(--white);font-family:var(--head);font-weight:700;display:flex;align-items:center;justify-content:center;border-radius:6px}
  .hero .btn-primary{left:111px;top:371px;width:170px;height:51px;font-size:15px}

  /* intro */
  .intro-title{position:absolute;top:801px;left:100px;width:1000px;text-align:center;font-weight:700;font-size:33px;line-height:48px;color:var(--ink)}
  .intro-art{position:absolute;left:72px;top:1037px;width:518px;height:438px;border-radius:40px;background:radial-gradient(circle at 50% 50%,#ffffff 0%,#ffe9c2 45%,#f9b43b 75%,#ffffff 100%)}
  .feature{position:absolute;left:653px;width:430px}
  .feature h3{font-weight:600;font-size:24px;color:var(--ink);margin-bottom:12px}
  .feature p{font-size:14px;line-height:26px;color:var(--text)}
  .feature-card{position:absolute;left:617px;top:1126px;width:472px;height:149px;background:var(--white);border-radius:6px;box-shadow:0 6px 22px rgba(0,0,0,.12);border-left:4px solid var(--orange)}

  /* promise band */
  .promise{top:1597px;height:411px;background:linear-gradient(90deg,#f3a017,#f7b33c 50%,#f3a017)}
  .promise h2{position:absolute;top:70px;left:80px;width:1040px;text-align:center;font-weight:700;font-size:34px;line-height:43px;color:var(--white)}
  .promise p{position:absolute;top:180px;left:300px;width:600px;text-align:center;font-size:14px;line-height:25px;color:var(--white)}

  /* pricing */
  .plan{position:absolute;top:1890px;width:436px;height:645px;background:var(--white);box-shadow:0 10px 30px rgba(0,0,0,.1);text-align:center}
  .plan h3{margin-top:54px;font-weight:700;font-size:23px}
  .plan-sub{margin:20px auto 0;width:330px;font-family:var(--head);font-weight:500;font-size:14px;line-height:26px;color:var(--ink);text-transform:uppercase}
  .plan-rule{margin:26px auto 0;width:374px;height:1px;background:var(--line)}
  .plan-price{font-family:var(--head);font-weight:600;font-size:15px;color:var(--ink)}
  .slider{position:absolute;left:44px;top:244px;width:364px;height:36px}
  .slider-labels{display:flex;justify-content:space-between;font-family:var(--head);font-weight:700;font-size:10px;color:var(--ink)}
  .slider-track{position:relative;margin-top:6px;height:6px;background:#e4e6ee;border-radius:3px}
  .slider-fill{position:absolute;left:0;top:0;width:122px;height:6px;background:var(--navy);border-radius:3px}
  .slider-knob{position:absolute;left:114px;top:-5px;width:16px;height:16px;border-radius:50%;background:var(--white);border:2px solid var(--navy)}
  .plan-credits{position:absolute;left:0;top:286px;width:100%;font-family:var(--head);font-weight:700;font-size:10px;color:var(--ink)}
  .plan .btn-primary{left:148px;top:327px;width:141px;height:38px;font-size:11px;border-radius:4px}
  .plan-list{position:absolute;left:64px;top:410px;list-style:none;text-align:left}
  .plan-list li{display:flex;align-items:center;gap:12px;height:37px;font-family:var(--head);font-weight:500;font-size:14px;color:var(--ink)}
  .plan-list svg{width:13px;height:13px;stroke:var(--orange);fill:none;stroke-width:3}

  /* how it works */
  .hiw-title{position:absolute;top:2626px;left:0;width:1200px;text-align:center;font-weight:700;font-size:33px}
  .step{position:absolute;top:2727px;width:293px;height:470px;background:var(--white);box-shadow:0 6px 22px rgba(0,0,0,.1);text-align:center}
  .step-art{height:179px;background:linear-gradient(135deg,#eef3ff 0%,#fbe9f3 55%,#fff4e2 100%)}
  .step-badge{position:absolute;left:18px;top:143px;width:56px;height:56px;border-radius:50%;background:var(--navy);color:var(--white);font-family:var(--head);font-weight:700;font-size:11px;line-height:14px;display:flex;flex-direction:column;align-items:center;justify-content:center;border:3px solid var(--white)}
  .step h3{margin:36px auto 0;width:250px;font-weight:700;font-size:22px;line-height:34px}
  .step p{margin:18px auto 0;width:240px;font-size:14px;line-height:30px;color:var(--text)}

  /* partners */
  .partners{top:3287px;height:386px;background:linear-gradient(100deg,#1a3a92,#244aa6 50%,#1a3a92)}
  .partners h2{position:absolute;top:72px;left:100px;width:1000px;text-align:center;font-weight:700;font-size:33px;line-height:43px;color:var(--white)}
  .partners p{position:absolute;top:184px;left:0;width:1200px;text-align:center;font-size:15px;color:var(--white)}
  .partner-row{position:absolute;top:244px;left:118px;width:964px;display:flex;justify-content:space-between;align-items:center}
  .partner{font-family:var(--head);font-weight:600;font-size:27px;color:var(--white)}

  /* faq */
  .faq-title{position:absolute;top:3748px;left:0;width:1200px;text-align:center;font-weight:700;font-size:33px}
  .faq-item{position:absolute;width:479px;background:var(--white);border-radius:8px;box-shadow:0 6px 22px rgba(0,0,0,.12);padding:0 62px 0 28px;display:flex;align-items:center;font-family:var(--head);font-weight:600;font-size:21px;line-height:30px;color:var(--ink)}
  .faq-toggle{position:absolute;right:22px;top:50%;margin-top:-10px;width:20px;height:20px}

  /* footer */
  .site-footer{top:4213px;height:395px;background:var(--footer);color:#d9dbe4}
  .site-footer .brand{left:113px;top:70px;color:var(--navy)}
  .footer-about{position:absolute;left:111px;top:170px;width:270px;font-size:14px;line-height:26px}
  .footer-col{position:absolute;top:92px}
  .footer-col h4{font-weight:700;font-size:18px;color:var(--white);margin-bottom:20px}
  .footer-col li{list-style:none;display:flex;gap:10px;font-size:14px;line-height:24px;margin-bottom:6px}
  .footer-col svg{flex:none;width:14px;height:14px;margin-top:5px;fill:#d9dbe4}
  .footer-social{display:flex;gap:12px}
  .footer-social span{width:30px;height:30px;border-radius:50%;background:var(--orange)}
  .footer-social span:first-child{background:var(--navy)}
  .copyright{position:absolute;left:0;top:4553px;width:1200px;text-align:center;font-size:14px;color:#d9dbe4}
</style>
</head>
<body>

<header class="topbar">
  <div class="topbar-left"></div>
  <div class="topbar-accent"></div>
  <div class="topbar-item" style="left:116px">
    <svg viewBox="0 0 24 24"><path d="M6.6 10.8a15.1 15.1 0 0 0 6.6 6.6l2.2-2.2a1 1 0 0 1 1-.25 11.4 11.4 0 0 0 3.6.57 1 1 0 0 1 1 1V20a1 1 0 0 1-1 1A17 17 0 0 1 3 4a1 1 0 0 1 1-1h3.5a1 1 0 0 1 1 1c0 1.25.2 2.45.57 3.57a1 1 0 0 1-.25 1z"/></svg>
    +1 555 010 2040
  </div>
  <div class="topbar-sep"></div>
  <div class="topbar-item" style="left:283px">
    <svg viewBox="0 0 24 24"><path d="M2 5h20v14H2zM3.5 6.5 12 13l8.5-6.5"/></svg>
    info@answercraft.com
  </div>
  <div class="topbar-login">&#10140; Login</div>
  <div class="topbar-divider"></div>
  <div class="topbar-social" aria-label="Social links"><span></span><span></span><span></span><span></span></div>
</header>

<header class="site-nav">
  <div class="brand"><span class="brand-mark"></span>AnswerCraft</div>
  <span class="nav-link" style="left:400px">Home</span>
  <span class="nav-link" style="left:481px">Why Reply?</span>
  <span class="nav-link" style="left:597px">How It Works</span>
  <span class="nav-link" style="left:726px">Pricing</span>
  <span class="nav-link" style="left:808px">Blog</span>
  <span class="nav-link" style="left:874px">Login</span>
  <a class="btn-try">Try Free</a>
</header>

<section class="hero" role="img" aria-label="Hand holding a phone with a five-star customer satisfaction rating overlay">
  <div class="hero-eyebrow">WELCOME TO</div>
  <h1 class="hero-title">WRITE REPLIES TO THE REVIEWS YOU GET ON SITES LIKE</h1>
  <a class="btn-primary">GET STARTED</a>
</section>

<h2 class="intro-title">IT'S SIMPLE. OUR TOOL WRITES REPLIES AND RE-SPONSES TO THE REVIEWS YOUR CUSTOMERS LEAVE. DOESN'T MATTER IF IT'S 1 OR 5 STARS.</h2>

<div class="intro-art" role="img" aria-label="Review card from a customer with a generated reply shown beneath it"></div>

<div class="feature" style="top:997px">
  <h3>Improved SEO</h3>
  <p>Searchly loves seeing you leave a reply to your reviews and will give you a boost in their search results and local SEO.</p>
</div>
<div class="feature-card"></div>
<div class="feature" style="top:1147px">
  <h3>Build Customer Trust</h3>
  <p>Customers want to know there are humans behind your com-panies product or service. Show them you value their time.</p>
</div>
<div class="feature" style="top:1306px">
  <h3>Increase Customer Loyalty</h3>
  <p>Taking the time to reply to a review shows your customers you care about them and their business. Show them some love!</p>
</div>
<div class="feature" style="top:1424px">
  <h3>Convert New Customers</h3>
  <p>FACT: Potential customers read reviews before making a deci-sion. Give a good first impression with personalized replies.</p>
</div>

<section class="promise">
  <h2>NEVER WORRY ABOUT HAVING TO COME UP WITH A UNIQUE RESPONSE TO EACH REVIEW EVER AGAIN!</h2>
  <p>If your business, product or service receives reviews, this tool will save you hundreds of hours.</p>
</section>

<div class="plan" style="left:138px">
  <h3>MONTHLY SUBSCRIPTIONS</h3>
  <p class="plan-sub">Perfect for getting started for one business/product</p>
  <div class="plan-rule"></div>
  <p class="plan-price" style="margin-top:26px">STARTS AT $9.99 / MONTH</p>
  <div class="slider">
    <div class="slider-labels"><span>50K</span><span>700+K</span></div>
    <div class="slider-track"><div class="slider-fill"></div><div class="slider-knob"></div></div>
  </div>
  <p class="plan-credits">5000 WORD CREDITS</p>
  <a class="btn-primary">START FOR FREE</a>
  <ul class="plan-list">
    <li><svg viewBox="0 0 16 16"><path d="M2 8.5 6 12l8-8"/></svg>Personalized responses</li>
    <li><svg viewBox="0 0 16 16"><path d="M2 8.5 6 12l8-8"/></svg>30+ Languages</li>
    <li><svg viewBox="0 0 16 16"><path d="M2 8.5 6 12l8-8"/></svg>Auto-Save</li>
    <li><svg viewBox="0 0 16 16"><path d="M2 8.5 6 12l8-8"/></svg>Revision History</li>
    <li><svg viewBox="0 0 16 16"><path d="M2 8.5 6 12l8-8"/></svg>Assign members usage limits</li>
  </ul>
</div>

<div class="plan" style="left:619px">
  <h3>AGENCY SUBSCRIPTIONS</h3>
  <p class="plan-sub">Perfect for multiple clients /products per month</p>
  <div class="plan-rule"></div>
  <p class="plan-price" style="margin-top:58px">STARTING AT $75.00 / MONTH</p>
  <a class="btn-primary">START FOR FREE</a>
  <ul class="plan-list">
    <li><svg viewBox="0 0 16 16"><path d="M2 8.5 6 12l8-8"/></svg>Everything in the Startup plan</li>
    <li><svg viewBox="0 0 16 16"><path d="M2 8.5 6 12l8-8"/></svg>Dedicated Account Manager</li>
    <li><svg viewBox="0 0 16 16"><path d="M2 8.5 6 12l8-8"/></svg>Onboarding &amp; Training</li>
    <li><svg viewBox="0 0 16 16"><path d="M2 8.5 6 12l8-8"/></svg>Unlimited Integrations</li>
  </ul>
</div>

<h2 class="hiw-title">HOW IT WORKS</h2>

<div class="step" style="left:111px">
  <div class="step-art" role="img" aria-label="Account sign-up screens with profile cards and reaction icons"></div>
  <div class="step-badge"><span>01</span><span>STEP</span></div>
  <h3>1 MINUTE ACCOUNT CREATION</h3>
  <p>If your facility needs equipment, they need it now. There are imme-diate, real world impacts for staff and residents without these sup-plies.</p>
</div>
<div class="step" style="left:445px">
  <div class="step-art" role="img" aria-label="Team members pasting a customer review into a dashboard"></div>
  <div class="step-badge"><span>02</span><span>STEP</span></div>
  <h3>WE MAKE IT WAY TOO SIMPLE!</h3>
  <p>Just copy the customer review and paste it into your account dash-board.</p>
</div>
<div class="step" style="left:780px">
  <div class="step-art" role="img" aria-label="Smiling user surrounded by generated reply cards from review sites"></div>
  <div class="step-badge"><span>03</span><span>STEP</span></div>
  <h3>ONLY A 10 SECOND WAIT</h3>
  <p>In just seconds you'll receive 3 unique and personal responses. Choose the reply you like best or tell our system to generate 3 more.</p>
</div>

<section class="partners">
  <h2>JOIN THOUSANDS OF LEADING BUSINESSES, BRANDS AND AGENCIES.</h2>
  <p>Write replies to the reviews you get on sites like:</p>
  <div class="partner-row">
    <span class="partner">Searchly</span>
    <span class="partner">Roomnest</span>
    <span class="partner">ReviewPath</span>
    <span class="partner">BuyHarbor</span>
    <span class="partner">TripNotes</span>
    <span class="partner">Localo</span>
    <span class="partner">Craftory</span>
  </div>
</section>

<h2 class="faq-title">FAQ</h2>
<div class="faq-item" style="left:107px;top:3846px;height:102px">Why is it important to respond to Searchly reviews?
  <svg class="faq-toggle" viewBox="0 0 20 20"><circle cx="10" cy="10" r="10" fill="#f5a111"/><path d="M10 5v10M5 10h10" stroke="#fff" stroke-width="2"/></svg></div>
<div class="faq-item" style="left:608px;top:3846px;height:102px">Why is it important to respond to negative reviews?
  <svg class="faq-toggle" viewBox="0 0 20 20"><circle cx="10" cy="10" r="10" fill="#f5a111"/><path d="M10 5v10M5 10h10" stroke="#fff" stroke-width="2"/></svg></div>
<div class="faq-item" style="left:107px;top:3973px;height:140px">How can I trust someone who doesn't work at my business to reply to reviews on my behalf?
  <svg class="faq-toggle" viewBox="0 0 20 20"><circle cx="10" cy="10" r="10" fill="#f5a111"/><path d="M10 5v10M5 10h10" stroke="#fff" stroke-width="2"/></svg></div>
<div class="faq-item" style="left:608px;top:3973px;height:102px">Which online review sites does AnswerCraft.com support?
  <svg class="faq-toggle" viewBox="0 0 20 20"><circle cx="10" cy="10" r="10" fill="#f5a111"/><path d="M10 5v10M5 10h10" stroke="#fff" stroke-width="2"/></svg></div>

<footer class="site-footer">
  <div class="brand"><span class="brand-mark"></span>AnswerCraft</div>
  <p class="footer-about">Lorem ipsum dolor sit amet, consec-tetur adipiscing elit, sed do eiusmod tempor incididunt ut labore</p>
  <div class="footer-col" style="left:411px;width:260px">
    <h4>CONTACT US</h4>
    <ul>
      <li><svg viewBox="0 0 24 24"><path d="M12 2a7 7 0 0 0-7 7c0 5 7 13 7 13s7-8 7-13a7 7 0 0 0-7-7zm0 9.5A2.5 2.5 0 1 1 12 6.5a2.5 2.5 0 0 1 0 5z"/></svg>110 Harbor Lane, Suite 4 Lorem ipsum dolor sit amet</li>
      <li><svg viewBox="0 0 24 24"><path d="M6.6 10.8a15.1 15.1 0 0 0 6.6 6.6l2.2-2.2a1 1 0 0 1 1-.25 11.4 11.4 0 0 0 3.6.57 1 1 0 0 1 1 1V20a1 1 0 0 1-1 1A17 17 0 0 1 3 4a1 1 0 0 1 1-1h3.5a1 1 0 0 1 1 1c0 1.25.2 2.45.57 3.57a1 1 0 0 1-.25 1z"/></svg>+1 555 010 2040</li>
      <li><svg viewBox="0 0 24 24"><path d="M2 5h20v14H2zm2 2v.5l8 6 8-6V7z" fill-rule="evenodd"/></svg>info@answercraft.com</li>
    </ul>
  </div>
  <div class="footer-col" style="left:717px">
    <h4>SUPPORT</h4>
    <ul>
      <li>Terms &amp; Conditions</li>
      <li>Contact us</li>
      <li>Privacy Policy</li>
      <li>About Us</li>
    </ul>
  </div>
  <div class="footer-col" style="left:910px">
    <h4>FOLLOW US</h4>
    <div class="footer-social" aria-label="Social links"><span></span><span></span><span></span><span></span></div>
  </div>
</footer>
<p class="copyright">©Copyrights 2023 AnswerCraft | &nbsp; All Rights Reserved</p>

</body>
</html>
```